Business Card Design

Business Card for professional consulting firm working with large financial institutions.

Target Market(s)

Executive buyers

Industry/Entity Type

Banking

Contact Information for Business Card

Mild creativity wanted. Not boring, but do elaborate artwork.

Font styles to use
Serif
Sans Serif

Colors

Designer to choose colors to be used in the design.

Requirements
Must have
• Standard business card features - company name, individual name, telephone, website, email, locations.
Nice to have
• Two colors
Should not have
• too many colors, fancy printing, cartoons.

```html
<!DOCTYPE html>
<html lang="en">
<head>
<meta charset="utf-8">
<title>Northgate Business Card</title>
<link rel="stylesheet" href="https://fonts.googleapis.com/css2?family=Roboto:wght@400;500&family=Roboto+Condensed:wght@500&family=Droid+Serif&family=Noto+Serif:wght@400&display=swap">
<style>
  :root {
    --bg: #e9e7e3;
    --paper: #f7f7f7;
    --ink: #1e1f20;
    --charcoal: #1d1f20;
    --grey: #b9b9b9;
    --soft-grey: #c9c9c9;
    --mid-grey: #6a6a6a;
    --white: #ffffff;
  }
  * { margin: 0; padding: 0; box-sizing: border-box; }
  html, body {
    width: 1200px; height: 886px; overflow: hidden;
    background: var(--bg);
  }
  .stage {
    width: 1200px; height: 886px;
    display: flex; align-items: center; justify-content: center; gap: 48px;
  }
  .card {
    width: 540px; height: 310px; position: relative; overflow: hidden;
    box-shadow: 0 10px 28px rgba(0,0,0,0.18);
  }
  /* Front */
  .card--front { background: var(--paper); }
  .front-brand {
    position: absolute; left: 0; top: 0; width: 270px; height: 310px;
    display: flex; align-items: center; justify-content: center;
  }
  .brand-name {
    font-family: "Noto Serif", serif; font-size: 40px; color: var(--soft-grey);
    letter-spacing: 0.5px;
  }
  .front-divider {
    position: absolute; left: 270px; top: 0; width: 1px; height: 310px;
    background: var(--grey);
  }
  .contact {
    position: absolute; left: 300px; top: 62px;
    font-family: "Roboto", sans-serif; color: var(--ink);
  }
  .contact-marker {
    position: absolute; left: 270px; top: 66px; width: 8px; height: 38px;
    background: var(--ink);
  }
  .person-name {
    font-family: "Roboto Condensed", sans-serif; font-weight: 500;
    font-size: 22px; letter-spacing: 0.3px; line-height: 1.1;
  }
  .person-role {
    font-family: "Roboto Condensed", sans-serif; font-size: 15px;
    color: var(--soft-grey); letter-spacing: 0.5px; margin-bottom: 16px;
  }
  .address { font-size: 13px; line-height: 1.5; color: var(--mid-grey); margin-bottom: 12px; }
  .contact-list { list-style: none; font-size: 13px; line-height: 1.75; color: var(--ink); }
  .contact-list li { display: flex; align-items: center; gap: 9px; }
  .contact-list svg { width: 11px; height: 11px; fill: var(--ink); flex: none; }
  /* Back */
  .card--back { background: var(--charcoal); }
  .back-band {
    position: absolute; left: 24px; top: 0; width: 26px; height: 310px;
    background: var(--grey);
  }
  .back-web {
    position: absolute; left: 74px; top: 155px;
    transform: translate(-50%, -50%) rotate(90deg);
    font-family: "Roboto", sans-serif; font-size: 10px; letter-spacing: 3px;
    color: var(--soft-grey); white-space: nowrap;
  }
  .back-brand {
    position: absolute; left: 100px; right: 0; top: 0; bottom: 0;
    display: flex; align-items: center; justify-content: center;
  }
  .back-brand .brand-name { color: var(--white); font-size: 46px; }
</style>
</head>
<body>
<main class="stage">
  <section class="card card--front" aria-label="Business card front">
    <div class="front-brand"><span class="brand-name">northgate</span></div>
    <div class="front-divider"></div>
    <div class="contact-marker"></div>
    <div class="contact">
      <p class="person-name">DANIEL REEVE</p>
      <p class="person-role">CEO/FOUNDER</p>
      <p class="address">2140 Harbor View Road<br>Juneau, Alaska 99801</p>
      <ul class="contact-list">
        <li><svg viewBox="0 0 24 24"><path d="M6.6 10.8a15 15 0 0 0 6.6 6.6l2.2-2.2a1 1 0 0 1 1-.25 11.4 11.4 0 0 0 3.6.57 1 1 0 0 1 1 1V20a1 1 0 0 1-1 1A17 17 0 0 1 3 4a1 1 0 0 1 1-1h3.5a1 1 0 0 1 1 1c0 1.25.2 2.45.57 3.57a1 1 0 0 1-.25 1z"/></svg>555 214 0398</li>
        <li><svg viewBox="0 0 24 24"><path d="M2 5h20v14H2z M4 7v1l8 5 8-5V7l-8 5z" fill-rule="evenodd"/></svg>info@northgatepartners.com</li>
        <li><svg viewBox="0 0 24 24"><circle cx="12" cy="12" r="10"/></svg>www.northgatepartners.com</li>
      </ul>
    </div>
  </section>
  <section class="card card--back" aria-label="Business card back">
    <div class="back-band"></div>
    <span class="back-web">www.northgatepartners.com</span>
    <div class="back-brand"><span class="brand-name">northgate</span></div>
  </section>
</main>
</body>
</html>
```